Brookvane Consulting Business Card Design

Business Card Design for Brookvane Consulting. Brookvane Consulting is a boutique consultancy based in Atlanta, GA., that specializes in marketing strategy, organization planning, and leadership development. We provide solutions for small businesses and startups as well as Vantage 300 companies.

http://brookvaneconsulting.com/

Target Market(s)

We provide solutions for small businesses and startups as well as Vantage 300 companies.

Industry/Entity Type

Consulting

Contact Information for Business Card

Two sided business card with priority on contact information, logo, tag line (Guidance to Aim Higher, Act Wiser, Grow Further)

Colors

Designer to choose colors to be used in the design.

Requirements
Must have
• contact information, logo, tag line (Guidance to Aim Higher, Act Wiser, Grow Further)
• Simple no over communication.
Nice to have
• I would like to see different placements of logo and creative use of both sides of the card
Should not have
• Do not put too much information on the card.

```html
<!DOCTYPE html>
<html lang="en">
<head>
<meta charset="utf-8">
<title>Brookvane Consulting Business Card</title>
<link rel="stylesheet" href="https://fonts.googleapis.com/css2?family=Poiret+One&family=Open+Sans:ital,wght@0,400;0,600;0,700;1,700&display=swap">
<style>
  :root {
    --backdrop: #e3e3e3;
    --card: #1c1d1f;
    --card-back-top: #2a2a2b;
    --card-back-bottom: #131314;
    --corner: #8a8a8a;
    --ink: #ffffff;
    --ink-soft: #d8d8d8;
  }
  * { margin: 0; padding: 0; box-sizing: border-box; }
  html, body {
    width: 1200px; height: 960px; overflow: hidden;
    background: var(--backdrop);
    font-family: "Open Sans", Arial, sans-serif;
  }
  .canvas { position: relative; width: 1200px; height: 960px; }
  .card {
    position: absolute;
    background: var(--card);
    box-shadow: 0 2px 4px rgba(0,0,0,0.25);
    overflow: hidden;
  }
  .card--front { left: 302px; top: 130px; width: 600px; height: 342px; }
  .card--back  { left: 300px; top: 489px; width: 598px; height: 341px; }

  .corner { position: absolute; }
  .corner--top-right { right: 0; top: 0; }
  .corner--bottom-left { left: 0; bottom: 0; }

  .holder-name {
    position: absolute; left: 42px; top: 30px;
    font-family: "Poiret One", "Century Gothic", sans-serif;
    font-weight: 400;
    font-size: 40px; color: var(--ink-soft); letter-spacing: 0.5px;
  }
  .holder-title {
    position: absolute; left: 46px; top: 73px;
    font-size: 12px; color: var(--ink-soft);
  }
  .contact-list {
    position: absolute; left: 46px; top: 101px;
    list-style: none; font-size: 14px; line-height: 19.5px; color: var(--ink-soft);
  }

  .brand-name {
    position: absolute; color: var(--ink);
    font-weight: 700; text-align: right; line-height: 1;
  }
  .card--front .brand-name { right: 56px; top: 222px; font-size: 33px; }
  .brand-name .brand-line { display: block; }
  .brand-name .brand-line--sub { font-size: 0.55em; letter-spacing: 2px; margin-top: 6px; }

  .back-pattern {
    position: absolute; inset: 0;
    background: linear-gradient(180deg, var(--card-back-top) 0%, #1e1e1f 55%, var(--card-back-bottom) 100%);
  }
  .card--back .brand-name {
    left: 0; right: 0; top: 128px; text-align: center; font-size: 48px;
  }
  .tagline {
    position: absolute; left: 0; right: 0; top: 271px;
    text-align: center; color: var(--ink);
    font-style: italic; font-weight: 700; font-size: 15px; line-height: 18px;
  }
</style>
</head>
<body>
<main class="canvas">
  <section class="card card--front" aria-label="Card front">
    <svg class="corner corner--top-right" width="90" height="90" viewBox="0 0 90 90"><polygon points="0,0 90,0 90,90" fill="var(--corner)"/></svg>
    <svg class="corner corner--bottom-left" width="88" height="88" viewBox="0 0 88 88"><polygon points="0,0 88,88 0,88" fill="var(--corner)"/></svg>
    <h1 class="holder-name">Darian Whitlock</h1>
    <p class="holder-title">Founder/Managing Director</p>
    <ul class="contact-list">
      <li>555-014-2290</li>
      <li>darian@brookvaneconsulting.com</li>
      <li>www.brookvaneconsulting.com</li>
    </ul>
    <p class="brand-name"><span class="brand-line">Brookvane</span><span class="brand-line brand-line--sub">CONSULTING</span></p>
  </section>

  <section class="card card--back" aria-label="Card back">
    <div class="back-pattern" role="img" aria-label="Faint repeating brand pattern covering the card back"></div>
    <p class="brand-name"><span class="brand-line">Brookvane</span><span class="brand-line brand-line--sub">CONSULTING</span></p>
    <p class="tagline">Guidance to Aim Higher<br>Act Wiser, Grow Further</p>
  </section>
</main>
</body>
</html>
```